Velmora Consulting Business

** Please add the content information from my old business card
1. I would like to see a two sided business card with both options with the 1st Option--Tallow Spire-new WHITE BACKGROUND LOGO
2 nd Option-Tallow Spire - new BLACK- Background Logo
3rd -Option a business card with my Photo on the card
Please add the new word to the card information:
EXECUTION
AS THE OWNER'S REP
WE AIM TO ACHIEVE YOUR
INFRASTRUCTURE VISION with
OUR SPECIALIZATION & EXECUTION in:

FUNDING Planning
BUSINESS Planning
INFRASTRUCTURE Planning
PROJECT Management
Since 2012
_____________________________________________________________________
I want to get spot uv raised printing. I was liking a a nice rich white linen paper stock with black writing & NOT A COLORED CARD other than a variety of white or black cards concept

```html
<!DOCTYPE html>
<html lang="en">
<head>
<meta charset="utf-8">
<title>Velmora Consulting – Business Card</title>
<link href="https://fonts.googleapis.com/css2?family=Arimo:wght@400;700&display=swap" rel="stylesheet">
<style>
  :root {
    --backdrop: #e4e4e2;
    --card: #2c2b30;
    --edge: #d8151b;
    --red: #e3191f;
    --white: #ffffff;
    --muted: #e9e9ea;
  }
  * { box-sizing: border-box; margin: 0; padding: 0; }
  html, body { width: 1200px; height: 801px; overflow: hidden; }
  body {
    background: var(--backdrop);
    font-family: "Arimo", Arial, sans-serif;
    color: var(--white);
    position: relative;
  }
  .card {
    position: absolute;
    width: 540px;
    height: 310px;
    background: var(--card);
    border-bottom: 4px solid var(--edge);
    border-left: 2px solid var(--edge);
    box-shadow: 0 10px 24px rgba(0,0,0,0.18);
    overflow: hidden;
  }
  .card-front { left: 40px; top: 110px; }
  .card-back { left: 620px; top: 380px; }

  /* brand lockup */
  .brand { display: flex; flex-direction: column; }
  .brand-row { display: flex; align-items: center; gap: 10px; }
  .brand-mark { width: 14px; height: 14px; background: var(--red); }
  .brand-name { font-weight: 700; color: var(--white); line-height: 1; letter-spacing: -1px; }
  .brand-sub { letter-spacing: 0.62em; font-weight: 400; color: var(--white); margin-top: 6px; }

  /* front */
  .front-top {
    position: absolute; left: 36px; top: 44px; right: 30px;
    display: flex; align-items: center;
  }
  .card-front .brand-name { font-size: 50px; }
  .card-front .brand-sub { font-size: 12px; }
  .divider { width: 1px; height: 86px; background: var(--muted); margin: 0 20px 0 22px; }
  .contacts { list-style: none; display: flex; flex-direction: column; gap: 9px; font-size: 14px; }
  .contacts li { display: flex; align-items: center; gap: 8px; }
  .contacts svg { width: 13px; height: 13px; flex: none; }
  .person { position: absolute; left: 36px; top: 180px; }
  .person-name { color: var(--red); font-weight: 700; font-size: 25px; }
  .person-title { font-size: 16px; margin-top: 6px; }
  .locations { font-size: 15px; margin-top: 22px; }

  /* back */
  .pitch {
    position: absolute; right: 26px; top: 20px; width: 360px;
    text-align: right; font-size: 14.5px; line-height: 1.2; text-transform: uppercase;
  }
  .pitch .accent { color: var(--red); font-weight: 700; }
  .pitch-rule { height: 1px; background: var(--red); margin: 5px 0 7px 30px; }
  .services { list-style: none; font-size: 14px; line-height: 1.36; }
  .services li { display: flex; justify-content: flex-end; align-items: center; gap: 8px; }
  .services li::after { content: ""; width: 8px; height: 8px; background: var(--red); }
  .services .svc { text-transform: uppercase; }
  .services .kind { text-transform: none; }
  .card-back .brand { position: absolute; left: 40px; top: 186px; }
  .card-back .brand-name { font-size: 58px; }
  .card-back .brand-sub { font-size: 13px; }
  .base-rule { position: absolute; left: 40px; right: 130px; top: 282px; height: 1px; background: var(--red); }
  .since-tag {
    position: absolute; right: 18px; top: 268px;
    background: var(--red); color: var(--white); font-size: 15px;
    padding: 6px 14px 6px 22px;
    clip-path: polygon(10px 0, 100% 0, 100% 100%, 10px 100%, 0 50%);
  }
</style>
</head>
<body>

<section class="card card-front" aria-label="Card front">
  <div class="front-top">
    <div class="brand">
      <div class="brand-row">
        <span class="brand-name">Velmora</span>
        <span class="brand-mark"></span>
      </div>
      <span class="brand-sub">CONSULTING</span>
    </div>
    <div class="divider"></div>
    <ul class="contacts">
      <li>
        <svg viewBox="0 0 16 16" aria-hidden="true"><path d="M4 1.5l2.3 3-1.4 1.6c.9 2 2.4 3.5 4.4 4.4l1.6-1.4 3 2.3-1.5 2.6C7 14 2 9 1.5 3z" fill="var(--red)"/></svg>
        <span>555.010.2748</span>
      </li>
      <li>
        <svg viewBox="0 0 16 16" aria-hidden="true"><rect x="1.5" y="3.5" width="13" height="9" fill="none" stroke="var(--red)" stroke-width="1.4"/><path d="M1.5 3.5L8 9l6.5-5.5" fill="none" stroke="var(--red)" stroke-width="1.4"/></svg>
        <span>noreen@velmora.ca</span>
      </li>
      <li>
        <svg viewBox="0 0 16 16" aria-hidden="true"><g fill="none" stroke="var(--red)" stroke-width="1.3"><circle cx="8" cy="8" r="6.3"/><ellipse cx="8" cy="8" rx="2.8" ry="6.3"/><path d="M1.7 8h12.6M2.8 4.8h10.4M2.8 11.2h10.4"/></g></svg>
        <span>www.velmora.ca</span>
      </li>
    </ul>
  </div>
  <div class="person">
    <p class="person-name">Noreen Ashcombe-Varela</p>
    <p class="person-title">CEO / Lead Project Manager</p>
    <p class="locations">Northgate NT • Harrowfield NB</p>
  </div>
</section>

<section class="card card-back" aria-label="Card back">
  <div class="pitch">
    <p>Execution</p>
    <p>As the <span class="accent">Owner's Rep</span></p>
    <p>We aim to achieve your</p>
    <p>Infrastructure vision <span style="text-transform:none">with</span></p>
    <p>Our specialization &amp; execution <span style="text-transform:none">in:</span></p>
    <div class="pitch-rule"></div>
    <ul class="services">
      <li><span><span class="svc">Funding</span> <span class="kind">Planning</span></span></li>
      <li><span><span class="svc">Business</span> <span class="kind">Planning</span></span></li>
      <li><span><span class="svc">Infrastructure</span> <span class="kind">Planning</span></span></li>
      <li><span><span class="svc">Project</span> <span class="kind">Management</span></span></li>
    </ul>
  </div>
  <div class="brand">
    <div class="brand-row">
      <span class="brand-name">Velmora</span>
      <span class="brand-mark"></span>
    </div>
    <span class="brand-sub">CONSULTING</span>
  </div>
  <div class="base-rule"></div>
  <div class="since-tag">Since 2012</div>
</section>

</body>
</html>
```